KRT Engineering Business Card Design

We’re looking for an elegant, clean, and timeless business card design that communicates experience, capability, and reliability.

KRT Engineering was established in 1995 , we are a Government Contracting company providing Professional Services to the Office of Frontier Affairs, Harbor Protection and the Vantage Collective. Our capabilities include: Acquisition & Program Management; Intelligence & Security Operations; Cyber, IT & Network Operations; Lifecycle Logistics & Asset Readiness; C5ISR Systems Engineering & Sustainment.

We want the card to reflect a straightforward, confident approach to business. The design should feel polished and professional without being flashy or overly corporate.

Design Direction
Clean, sophisticated, and uncluttered
Elegant but understated
Strong typography and thoughtful spacing
A timeless aesthetic rather than something overly trendy
Confident and established, with a sense of substance
Easy to read and practical in a real-world business setting

The overall impression should be: “These are experienced professionals who know what they’re doing, do what they say, and can be relied upon.”

We’re open to creative interpretations. The finished card should feel distinctive through its typography, proportions, layout, and attention to detail rather than through excessive graphics or visual effects.

We’re looking for a design that would make a potential client immediately feel that they’re dealing with a capable, trustworthy, and established company.

Company Colors: Navy and Gold/Yellow (but you do not need to use these colors on the card)
Company Name: KRT Engineering Associates, Inc. (known as KRT Engineering)
Website: krtengineering.com
Company Logo: Navy & Gold (other variations attached)

```html
<!DOCTYPE html>
<html lang="en">
<head>
<meta charset="utf-8">
<title>KRT Engineering Business Card</title>
<link rel="stylesheet" href="https://fonts.googleapis.com/css2?family=Poppins:wght@400;500;700&family=Allura&display=swap">
<style>
  :root {
    --navy: #1b2552;
    --gold: #f5e54a;
    --gold-shade: #c9b43a;
    --white: #ffffff;
    --backdrop: #d9d9d9;
  }
  * { margin: 0; padding: 0; box-sizing: border-box; }
  html, body { width: 1200px; height: 2185px; overflow: hidden; background: var(--backdrop); }
  body { position: relative; font-family: "Poppins", sans-serif; color: var(--navy); }

  .card { position: absolute; left: 98px; width: 1005px; height: 574px; overflow: hidden; }
  .card--front { top: 496px; }
  .card--back { top: 1115px; }
  .card__shape { position: absolute; inset: 0; }

  .wordmark { position: absolute; display: flex; align-items: center; font-weight: 700;
    letter-spacing: -1px; line-height: 1; white-space: nowrap; }
  .wordmark__dot { border-radius: 50%; background: var(--gold); flex: none; }
  .card--front .wordmark { left: 60px; top: 258px; color: var(--white); font-size: 50px; gap: 14px; }
  .card--front .wordmark__dot { width: 30px; height: 30px; }
  .card--back .wordmark { left: 40px; top: 168px; color: var(--navy); font-size: 40px; gap: 12px; }
  .card--back .wordmark__dot { width: 26px; height: 26px; }

  .contact { position: absolute; left: 0; top: 0; }
  .contact__row { position: absolute; display: flex; align-items: center; }
  .contact__icon { width: 50px; height: 50px; border-radius: 50%; background: var(--gold);
    border: 4px solid var(--white); display: flex; align-items: center; justify-content: center; }
  .contact__text { position: absolute; font-size: 22px; font-weight: 500; white-space: nowrap; line-height: 1.2; }
  .contact__rule { position: absolute; left: 640px; width: 290px; border-top: 1px dashed #efe6a0; }

  .ribbon-text { position: absolute; font-weight: 500; font-size: 21px; letter-spacing: 5px; }

  .years { position: absolute; left: 35px; top: 396px; font-family: "Allura", cursive;
    font-size: 62px; line-height: 1; color: var(--navy); white-space: nowrap; }
  .years-tagline { position: absolute; left: 262px; top: 415px; font-size: 14px; font-weight: 500;
    line-height: 1.3; text-transform: uppercase; white-space: nowrap; }

  .services { position: absolute; left: 0; top: 0; list-style: none; }
  .service { position: absolute; left: 530px; width: 460px; display: flex; align-items: center; }
  .service__icon { width: 44px; height: 44px; border-radius: 50%; background: var(--gold); flex: none; }
  .service__label { margin-left: 26px; font-size: 24px; font-weight: 500; line-height: 1.22;
    color: var(--white); text-transform: uppercase; white-space: nowrap; }
  .service-rule { position: absolute; left: 600px; width: 332px; border-top: 1.5px solid var(--gold); }
</style>
</head>
<body>

<section class="card card--front" aria-label="Card front">
  <svg class="card__shape" viewBox="0 0 1005 574" width="1005" height="574" aria-hidden="true">
    <rect width="1005" height="574" fill="var(--navy)"/>
    <path d="M672 0 C600 120 610 260 670 380 C705 460 705 520 665 574 L1005 574 L1005 0 Z" fill="var(--white)"/>
    <path d="M626 0 C560 120 572 260 628 380 C668 460 662 520 622 574" fill="none" stroke="var(--white)" stroke-width="14"/>
    <polygon points="551,381 597,352 597,381" fill="var(--gold-shade)"/>
    <polygon points="551,381 1005,381 1005,447 562,447" fill="var(--gold)"/>
  </svg>

  <div class="wordmark"><span class="wordmark__dot"></span>KRT Engineering</div>

  <div class="contact">
    <div class="contact__row" style="left:570px; top:115px;">
      <span class="contact__icon">
        <svg width="24" height="24" viewBox="0 0 24 24" aria-hidden="true"><path d="M6.6 10.8a15 15 0 0 0 6.6 6.6l2.2-2.2c.3-.3.7-.4 1-.2 1.1.4 2.3.6 3.6.6.6 0 1 .4 1 1V20c0 .6-.4 1-1 1C10.6 21 3 13.4 3 4c0-.6.4-1 1-1h3.5c.6 0 1 .4 1 1 0 1.3.2 2.5.6 3.6.1.3 0 .7-.2 1z" fill="var(--navy)"/></svg>
      </span>
    </div>
    <div class="contact__text" style="left:640px; top:126px;">555 010 4821</div>
    <div class="contact__rule" style="top:180px;"></div>

    <div class="contact__row" style="left:577px; top:190px;">
      <span class="contact__icon">
        <svg width="26" height="26" viewBox="0 0 24 24" aria-hidden="true"><circle cx="12" cy="12" r="9" fill="none" stroke="var(--navy)" stroke-width="2"/><ellipse cx="12" cy="12" rx="4" ry="9" fill="none" stroke="var(--navy)" stroke-width="2"/><path d="M3 12h18M5 7.5h14M5 16.5h14" stroke="var(--navy)" stroke-width="1.6"/></svg>
      </span>
    </div>
    <div class="contact__text" style="left:646px; top:200px;">krtengineering.com</div>
    <div class="contact__rule" style="top:243px;"></div>

    <div class="contact__row" style="left:596px; top:268px;">
      <span class="contact__icon">
        <svg width="22" height="26" viewBox="0 0 24 28" aria-hidden="true"><path d="M12 1a9 9 0 0 0-9 9c0 7 9 17 9 17s9-10 9-17a9 9 0 0 0-9-9zm0 12.5a3.5 3.5 0 1 1 0-7 3.5 3.5 0 0 1 0 7z" fill="var(--navy)"/></svg>
      </span>
    </div>
    <div class="contact__text" style="left:666px; top:262px;">1420 Harbor Point Drive, Suite<br>310 Norfield, VA 20145</div>
  </div>

  <div class="ribbon-text" style="left:671px; top:399px;">ESTABLISHED 1995</div>
</section>

<section class="card card--back" aria-label="Card back">
  <svg class="card__shape" viewBox="0 0 1005 574" width="1005" height="574" aria-hidden="true">
    <rect width="1005" height="574" fill="var(--white)"/>
    <path d="M437 0 C500 150 505 300 468 420 C448 490 445 540 486 574 L1005 574 L1005 0 Z" fill="var(--navy)"/>
    <path d="M405 0 C462 150 458 300 420 420 C402 490 398 540 418 574" fill="none" stroke="var(--navy)" stroke-width="24"/>
    <polygon points="448,381 492,402 448,402" fill="var(--gold-shade)"/>
    <polygon points="0,402 492,402 480,470 0,470" fill="var(--gold)"/>
  </svg>

  <div class="wordmark"><span class="wordmark__dot"></span>KRT Engineering</div>

  <div class="years">30 Years</div>
  <div class="years-tagline">Cleared expertise with<br>measurable impact</div>

  <ul class="services">
    <li class="service" style="top:82px;"><span class="service__icon"></span><span class="service__label">Acquisition &amp; Program<br>Management</span></li>
    <li class="service" style="top:170px;"><span class="service__icon"></span><span class="service__label">Intelligence &amp; Security<br>Operations</span></li>
    <li class="service" style="top:258px;"><span class="service__icon"></span><span class="service__label">Cyber, IT &amp; Network<br>Operations</span></li>
    <li class="service" style="top:349px;"><span class="service__icon"></span><span class="service__label">Lifecycle Logistics &amp;<br>Asset Readiness</span></li>
    <li class="service" style="top:436px;"><span class="service__icon"></span><span class="service__label">C5ISR Systems Engineering<br>&amp; Sustainment</span></li>
  </ul>
  <div class="service-rule" style="top:154px;"></div>
  <div class="service-rule" style="top:242px;"></div>
  <div class="service-rule" style="top:334px;"></div>
  <div class="service-rule" style="top:423px;"></div>
</section>

</body>
</html>
```